Banner Ad Design Project

We need banner ads for a website size:
728 x 90
160 x 90

Look at our website and you can see the color green we use throughout our advertising.

We have copy for 4 ads that should be interchangable

1. EHR me ASAP. Sign up in minutes.
2. Connect. Collaborate. Immediate. Sign up in minutes.
3. No software. No downloads. No charge.
4. EMR + HIE + PMR = FREE

Target Market(s)

Physicians

Industry/Entity Type

Software

```html
<!DOCTYPE html>
<html lang="en">
<head>
<meta charset="utf-8">
<title>Cellora Health – Banner Ads</title>
<link href="https://fonts.googleapis.com/css2?family=PT+Sans:wght@400;700&display=swap" rel="stylesheet">
<style>
  :root {
    --stage: #e7e4df;
    --green: #8fc64a;
    --green-light: #a9d66c;
    --green-pale: #c4e49a;
    --green-dark: #5f7d48;
    --white: #ffffff;
    --logo-text: #7aa83b;
    --photo-a: #8a98b6;
    --photo-b: #dcdad4;
  }
  * { margin: 0; padding: 0; box-sizing: border-box; }
  html, body {
    width: 1200px; height: 900px; overflow: hidden;
    background: var(--stage);
    font-family: "PT Sans", "Arial Narrow", sans-serif;
  }
  .banner {
    position: absolute;
    overflow: hidden;
    background: linear-gradient(180deg, var(--green-light) 0%, var(--green) 78%, var(--green-pale) 78%, var(--green-pale) 100%);
  }
  .banner--small { left: 30px; top: 267px; width: 252px; height: 141px; }
  .banner--leader { left: 30px; top: 435px; width: 1143px; height: 143px; }

  .brand {
    position: absolute;
    background: var(--white);
    display: flex; align-items: center; justify-content: center; gap: 8px;
    color: var(--logo-text);
    font-weight: 700;
    white-space: nowrap;
  }
  .brand__dot { border-radius: 50%; background: var(--logo-text); flex: none; }
  .banner--small .brand {
    right: 0; top: 0; width: 165px; height: 50px;
    border-bottom-left-radius: 10px;
    font-size: 20px;
  }
  .banner--small .brand__dot { width: 12px; height: 12px; }
  .banner--leader .brand {
    left: 4px; top: 12px; width: 249px; height: 119px;
    border-radius: 10px;
    box-shadow: 0 2px 4px rgba(0,0,0,0.25);
    font-size: 31px;
  }
  .banner--leader .brand__dot { width: 18px; height: 18px; }

  .headline { position: absolute; color: var(--white); font-weight: 700; line-height: 1.2; }
  .banner--small .headline { left: 22px; top: 62px; font-size: 20px; }
  .banner--leader .headline { left: 280px; top: 34px; font-size: 31px; line-height: 1.25; }

  .cta {
    position: absolute; left: 675px; top: 18px; width: 117px; height: 105px;
    background: var(--green-dark);
    border: 3px solid var(--green-pale);
    border-radius: 14px;
    box-shadow: 0 2px 5px rgba(0,0,0,0.3);
    color: var(--white);
    font-size: 22px; line-height: 1.3; text-align: center;
    padding-top: 16px;
  }
  .cta__arrow { display: block; margin: 4px auto 0; }

  .team-photo {
    position: absolute; right: 0; top: 3px; width: 318px; height: 140px;
    background: linear-gradient(90deg, var(--photo-a) 0%, var(--photo-b) 100%);
  }
</style>
</head>
<body>
  <section class="banner banner--small">
    <div class="brand"><span class="brand__dot"></span>Cellora Health</div>
    <p class="headline">EHR me ASAP<br>Sign up in minutes</p>
  </section>

  <section class="banner banner--leader">
    <div class="brand"><span class="brand__dot"></span>Cellora Health</div>
    <p class="headline">EHR me ASAP<br>Sign up in minutes</p>
    <div class="cta">Sign Up<br>For Free
      <svg class="cta__arrow" width="16" height="12" viewBox="0 0 16 12"><polygon points="0,0 16,0 8,12" fill="#a9d66c"/></svg>
    </div>
    <div class="team-photo" role="img" aria-label="Photo of a group of smiling doctors and nurses in white coats and scrubs"></div>
  </section>
</body>
</html>
```